New Business Card Design

We would like to refresh our business cards and make them look better. We are an IT company specialising in Cloud Services, IT Managed Services, software and hardware. I have attached a PSD of our current design. Also attached our logo.
Updates

I have uploaded all new logos in EPS format.

Can you please edit all designs to include a job title for Marcus Hollis, eg. General Manager

Industry/Entity Type

Software

Colors
ffffff

Requirements
Must have
• Please use white background.
Should not have
• Black background

```html
<!DOCTYPE html>
<html lang="en">
<head>
<meta charset="utf-8">
<title>Meridian Technology – Business Card</title>
<link rel="stylesheet" href="https://fonts.googleapis.com/css2?family=Open+Sans:wght@400;600;700&display=swap">
<style>
  :root {
    --page: #e9e6e1;
    --card-white: #ffffff;
    --brand-red: #c23a2a;
    --brand-grey: #8a939c;
    --ink: #222222;
    --ink-soft: #444444;
    --on-red: #ffffff;
    --on-red-soft: #f3d2cc;
  }
  * { box-sizing: border-box; margin: 0; padding: 0; }
  html, body {
    width: 1200px; height: 720px; overflow: hidden;
    background: var(--page);
    font-family: "Open Sans", Arial, sans-serif;
  }
  .canvas {
    position: relative; width: 1200px; height: 720px;
  }
  .card {
    position: absolute; top: 200px;
    width: 540px; height: 310px;
    border-radius: 6px;
    box-shadow: 0 6px 18px rgba(0,0,0,0.18);
    overflow: hidden;
  }
  /* Front */
  .card-front { left: 40px; background: var(--card-white); }
  .front-tab-right {
    position: absolute; right: -10px; top: 120px;
    width: 22px; height: 40px; border-radius: 8px;
    background: var(--brand-red);
  }
  .front-tab-left {
    position: absolute; left: -10px; top: 200px;
    width: 22px; height: 80px; border-radius: 8px;
    background: var(--brand-grey); opacity: 0.7;
  }
  .brand {
    position: absolute; left: 40px; top: 46px;
    display: flex; align-items: center; gap: 14px;
  }
  .brand-dot {
    width: 38px; height: 38px; border-radius: 50%;
    background: var(--brand-red);
  }
  .brand-name {
    font-size: 30px; font-weight: 400; letter-spacing: 3px;
    color: var(--brand-grey); text-transform: lowercase;
  }
  .person {
    position: absolute; right: 36px; top: 122px; text-align: right;
  }
  .person-name {
    font-size: 17px; font-weight: 700; color: var(--brand-red);
  }
  .person-title {
    font-size: 13px; font-weight: 400; color: var(--ink); margin-top: 2px;
  }
  .contact {
    position: absolute; left: 40px; bottom: 34px;
    list-style: none; font-size: 14px; color: var(--ink-soft);
  }
  .contact li {
    display: flex; align-items: center; gap: 10px; line-height: 22px;
  }
  .contact svg { width: 13px; height: 13px; flex: none; }
  /* Back */
  .card-back { left: 620px; background: var(--brand-red); text-align: center; }
  .back-brand {
    position: absolute; left: 0; right: 0; top: 70px;
    display: flex; flex-direction: column; align-items: center; gap: 16px;
  }
  .back-dot {
    width: 84px; height: 84px; border-radius: 50%;
    background: var(--card-white);
  }
  .back-brand-name {
    font-size: 24px; font-weight: 400; letter-spacing: 3px;
    color: var(--on-red); text-transform: lowercase;
  }
  .tagline {
    position: absolute; left: 0; right: 0; top: 222px;
    font-size: 15px; line-height: 21px; color: var(--on-red);
  }
  .back-url {
    position: absolute; left: 0; right: 0; bottom: 18px;
    font-size: 12px; letter-spacing: 3px; color: var(--on-red-soft);
  }
</style>
</head>
<body>
<main class="canvas">

  <section class="card card-front" aria-label="Business card front">
    <div class="front-tab-right"></div>
    <div class="front-tab-left"></div>

    <div class="brand">
      <span class="brand-dot"></span>
      <span class="brand-name">meridian technology</span>
    </div>

    <div class="person">
      <p class="person-name">Marcus Hollis</p>
      <p class="person-title">General Manager</p>
    </div>

    <ul class="contact">
      <li>
        <svg viewBox="0 0 16 16" aria-hidden="true"><circle cx="8" cy="8" r="8" fill="#c23a2a"/><path d="M5 4.5c.6-.5 1.2-.4 1.5.2l.6 1.2c.2.4 0 .8-.3 1l-.5.4c.5 1 1.2 1.7 2.2 2.2l.4-.5c.3-.3.7-.5 1-.3l1.2.6c.6.3.7.9.2 1.5-.6.7-1.6.9-2.6.4C6.8 10.3 5.6 9.1 4.8 7.2c-.4-1-.3-2 .2-2.7z" fill="#fff"/></svg>
        07 5550 1234
      </li>
      <li>
        <svg viewBox="0 0 16 16" aria-hidden="true"><rect x="4" y="1" width="8" height="14" rx="1.5" fill="#c23a2a"/><rect x="5.5" y="3" width="5" height="7" fill="#fff"/><circle cx="8" cy="12.5" r="0.9" fill="#fff"/></svg>
        0400 555 017
      </li>
      <li>
        <svg viewBox="0 0 16 16" aria-hidden="true"><rect x="1" y="3" width="14" height="10" rx="1.5" fill="#c23a2a"/><path d="M2 4.5l6 4.5 6-4.5" stroke="#fff" stroke-width="1.3" fill="none"/></svg>
        hollism@meridianit.com.au
      </li>
      <li>
        <svg viewBox="0 0 16 16" aria-hidden="true"><circle cx="8" cy="8" r="7" fill="#c23a2a"/><g stroke="#fff" stroke-width="1" fill="none"><ellipse cx="8" cy="8" rx="3" ry="6"/><path d="M2 8h12M3 5h10M3 11h10"/></g></svg>
        www.meridianit.com.au
      </li>
    </ul>
  </section>

  <section class="card card-back" aria-label="Business card back">
    <div class="back-brand">
      <span class="back-dot"></span>
      <span class="back-brand-name">meridian technology</span>
    </div>
    <p class="tagline">We are an IT company specializing in Cloud Services<br>IT Managed Services, software and hardware</p>
    <p class="back-url">www.meridianit.com.au</p>
  </section>

</main>
</body>
</html>
```